Blow Dry Bar Business Cards

These cards must be eye catching and modern.
You must be willing to work fast and make changes.

Winner will be offered other projects

Files 1 THIS IS THE STYLE CARDS I AM INTRESTED IN!!!
Please be creative, I am paying for my own eye catching design. I need files to be nexa press ready.

COLORS THAT ARE PAINTED INSIDE MY SHOP:
- - - http://www.quorvelpaint.example/en/explore-colors/painter/color-selector.html?colors=4007-3C

- - - http://www.brandivex.example/color/paint-colors/hidden-corridor-d58-2

I want the business cards sleek and modern if you use the logo please correct imperfections. I added the part that says Blow Dry Bar (see website).
Do not be afraid to separate the blow dryer from the name to make the cards look like the file with the pink elephant.

SHOULD INCLUDE
*Blow Dryer (we are a blow dry bar not a salon we do not cut or color so do not include sheers of any kind)
*BUSINESS NAME: Simply Swept Upward - Blow Dry Bar (PLEASE SEE MY WEBSITE)
* Website: SIMPLYSWEPTUPWARD.EXAMPLE
*Phone number (555) 014-2763
Updates

Nexa press said it can be submitted in JPG

http://www.brandivex.example/color/paint-colors/hidden-corridor-d58-2 http://www.quorvelpaint.example/en/explore-colors/painter/color-selector.html?colors=4007-3C ^^^^ These links will take you to the color paint that is painted inside my shop.

Target Market(s)

AGES 18 - 55 WOMEN
HIGH END MARKET

Industry/Entity Type

Salon

Requirements
Must have
• SEE COLOR EXAMPLE FILE
BLOW DRYER
UNIQUE
I LIKE THE CARD WITH THE PINK ELEPHANT THE BEST
Nice to have
• BE AS CREATIVE AND MODERN AS POSSIBLE DO NOT COPY ANY OF THE CARDS BELOW.
Should not have
• SCISSORS
PINK

```html
<!DOCTYPE html>
<html lang="en">
<head>
<meta charset="utf-8">
<title>Swept Upward Blow Dry Bar – Business Cards</title>
<link rel="stylesheet" href="https://fonts.googleapis.com/css2?family=Roboto+Slab:wght@300;400&family=Lato:wght@300;400&family=Raleway:wght@400&display=swap">
<style>
  :root {
    --backdrop: #e7e4de;
    --charcoal: #2f3032;
    --lime: #dce46c;
    --stripe: #9b9c9c;
    --ink: #3a3b3c;
    --shadow: rgba(0, 0, 0, 0.22);
  }
  * { margin: 0; padding: 0; box-sizing: border-box; }
  html, body { width: 1200px; height: 858px; overflow: hidden; }
  body {
    background: var(--backdrop);
    position: relative;
    font-family: "Lato", sans-serif;
  }
  .card {
    position: absolute;
    width: 620px;
    height: 354px;
    background: var(--charcoal);
    border-radius: 4px;
    overflow: hidden;
    box-shadow: 0 10px 24px var(--shadow);
  }
  .card--front { left: 120px; top: 40px; }
  .card--back { left: 460px; top: 464px; }

  /* front */
  .front-brand {
    position: absolute;
    left: 0; top: 0; right: 0; height: 212px;
    display: flex; flex-direction: column; align-items: center; justify-content: center;
  }
  .brand-row { display: flex; align-items: center; gap: 18px; }
  .brand-dot {
    width: 22px; height: 22px; border-radius: 50%;
    background: var(--lime);
  }
  .brand-name {
    font-family: "Roboto Slab", serif;
    font-weight: 300;
    font-size: 60px;
    color: var(--lime);
    letter-spacing: 1px;
    line-height: 1;
  }
  .brand-tagline {
    margin-top: 10px;
    font-family: "Lato", sans-serif;
    font-weight: 300;
    font-size: 26px;
    color: var(--lime);
    letter-spacing: 0.5px;
  }
  .front-stripe {
    position: absolute; left: 0; right: 0; top: 212px; height: 14px;
    background: var(--stripe);
  }
  .front-band {
    position: absolute; left: 0; right: 0; top: 226px; bottom: 0;
    background: var(--lime);
    display: flex; align-items: center;
  }
  .owner-names {
    width: 290px;
    text-align: center;
    font-family: "Roboto Slab", serif;
    font-weight: 300;
    font-size: 30px;
    color: var(--ink);
  }
  .band-divider {
    width: 1px; height: 78px; background: var(--ink); opacity: 0.5;
  }
  .contact-list {
    list-style: none;
    padding-left: 26px;
    display: flex; flex-direction: column; gap: 9px;
  }
  .contact-item {
    display: flex; align-items: center; gap: 10px;
    font-family: "Raleway", sans-serif;
    font-size: 13px;
    letter-spacing: 0.6px;
    color: var(--ink);
  }
  .contact-icon {
    width: 20px; height: 20px;
    background: var(--ink);
    border-radius: 2px;
    display: flex; align-items: center; justify-content: center;
    flex: none;
  }

  /* back */
  .back-brand {
    position: absolute; left: 0; right: 0; top: 0; height: 272px;
    display: flex; align-items: center; justify-content: center;
  }
  .back-brand .brand-name { font-size: 66px; }
  .back-band {
    position: absolute; left: 0; right: 0; bottom: 0; height: 82px;
    background: var(--lime);
    display: flex; align-items: center; justify-content: center;
  }
  .back-web {
    font-family: "Raleway", sans-serif;
    font-size: 18px;
    letter-spacing: 1.2px;
    color: var(--ink);
  }
</style>
</head>
<body>

  <section class="card card--front" aria-label="Business card front">
    <div class="front-brand">
      <div class="brand-row">
        <span class="brand-name">Swept Upward</span>
        <span class="brand-dot"></span>
      </div>
      <div class="brand-tagline">Blow Dry Bar</div>
    </div>
    <div class="front-stripe"></div>
    <div class="front-band">
      <div class="owner-names">Maren&amp;Tove</div>
      <div class="band-divider"></div>
      <ul class="contact-list">
        <li class="contact-item">
          <span class="contact-icon">
            <svg width="12" height="12" viewBox="0 0 12 12"><path d="M2.5 1 L4.5 1 L5.3 3.6 L4 4.6 Q5 7 7.4 8 L8.4 6.7 L11 7.5 L11 9.5 Q11 11 9.5 11 Q1 10 1 2.5 Q1 1 2.5 1 Z" fill="var(--lime)"/></svg>
          </span>
          (555) 014-2763
        </li>
        <li class="contact-item">
          <span class="contact-icon">
            <svg width="12" height="12" viewBox="0 0 12 12" fill="none" stroke="var(--lime)" stroke-width="1"><circle cx="6" cy="6" r="5"/><ellipse cx="6" cy="6" rx="2.2" ry="5"/><line x1="1" y1="6" x2="11" y2="6"/></svg>
          </span>
          SIMPLYSWEPTUPWARD.EXAMPLE
        </li>
        <li class="contact-item">
          <span class="contact-icon">
            <svg width="12" height="10" viewBox="0 0 12 10" fill="none" stroke="var(--lime)" stroke-width="1"><rect x="0.5" y="0.5" width="11" height="9"/><polyline points="0.5,0.5 6,5.5 11.5,0.5"/></svg>
          </span>
          INFO@SIMPLYSWEPTUPWARD.EXAMPLE
        </li>
      </ul>
    </div>
  </section>

  <section class="card card--back" aria-label="Business card back">
    <div class="back-brand">
      <div class="brand-row">
        <span class="brand-name">Swept Upward</span>
        <span class="brand-dot"></span>
      </div>
    </div>
    <div class="back-band">
      <span class="back-web">SIMPLYSWEPTUPWARD.EXAMPLE</span>
    </div>
  </section>

</body>
</html>
```